Design a website for a quickly growing ghostwriting and editing firm

DWB Productions has a website through Wix, but we need help! We are based in Austin, TX, and we work primarily with self-help, wellness, and diet authors. We offer ghostwriting, editing and book development services. You can see our basic site now at www.dorawhitbyproductions.com

```html
<!DOCTYPE html>
<html lang="en">
<head>
<meta charset="UTF-8">
<title>DWB Productions</title>
<link href="https://fonts.googleapis.com/css2?family=Quicksand:wght@400;500;600;700&family=Open+Sans:wght@400;600&display=swap" rel="stylesheet">
<style>
:root{
  --orange:#c0691f;
  --orange-dark:#a9561a;
  --brown:#6b3410;
  --brown-deep:#5a2a0c;
  --beige:#ead7c6;
  --cream:#f6ece3;
  --grey-bg:#efefef;
  --text:#6f6f6f;
  --ink:#3b2a1e;
  --white:#ffffff;
}
*{margin:0;padding:0;box-sizing:border-box}
html,body{width:1200px;height:3748px;overflow:hidden}
body{font-family:"Open Sans",sans-serif;color:var(--text);background:var(--white);position:relative}
.h{font-family:"Quicksand",sans-serif}
section,header,footer{position:absolute;left:0;width:1200px}
.btn{display:inline-block;font-family:"Quicksand",sans-serif;font-weight:600;font-size:15px;border-radius:30px;text-align:center}
p{font-size:14px;line-height:1.75}

/* hero */
.hero{top:0;height:620px;background:linear-gradient(90deg,#e5cdb9 0%,var(--beige) 45%,#f1e2d5 100%)}
.brand{position:absolute;left:112px;top:22px;display:flex;align-items:center;gap:14px}
.brand-dot{width:70px;height:70px;border-radius:50%;background:var(--orange)}
.brand-name{font-family:"Quicksand",sans-serif;font-weight:700;font-size:22px;color:var(--ink);line-height:1.1;letter-spacing:1px}
.nav{position:absolute;top:56px;right:112px;display:flex;gap:30px;font-family:"Quicksand",sans-serif;font-weight:600;font-size:14px;color:var(--ink)}
.nav .active{color:var(--orange)}
.hero-title{position:absolute;left:112px;top:262px;font-family:"Quicksand",sans-serif;font-weight:700}
.hero-title .name{font-size:38px;color:var(--ink);letter-spacing:1px}
.hero-title .co{font-size:60px;color:var(--orange);line-height:1.05;letter-spacing:1px}
.hero-text{position:absolute;left:112px;top:405px;width:420px;font-size:13px;color:var(--orange-dark)}
.hero .btn{position:absolute;left:112px;top:502px;width:160px;height:52px;line-height:52px;background:var(--brown);color:var(--white)}
.hero-art{position:absolute;left:630px;top:130px;width:470px;height:470px;border-radius:6px;background:linear-gradient(160deg,#f8f3ee 0%,#e7d3c0 60%,#c89a70 100%)}

/* about */
.about{top:620px;height:680px}
.about-photo{position:absolute;left:148px;top:196px;width:292px;height:292px;border-radius:50%;border:8px solid var(--orange);background:linear-gradient(160deg,#8a6a52,#3d2e28)}
.section-title{font-family:"Quicksand",sans-serif;font-weight:600;font-size:40px;color:var(--orange);letter-spacing:1px}
.about .section-title{position:absolute;left:620px;top:210px}
.about .rule{position:absolute;left:620px;top:270px;width:480px;height:2px;background:var(--orange)}
.about p{position:absolute;left:620px;top:296px;width:470px;font-size:13px}
.about .btn{position:absolute;left:620px;top:538px;width:160px;height:52px;line-height:52px;background:var(--orange);color:var(--white)}

/* services */
.services{top:1300px;height:580px;background:linear-gradient(180deg,var(--orange) 0%,var(--orange-dark) 100%)}
.services-title{position:absolute;top:60px;left:0;width:1200px;text-align:center;color:var(--white);font-family:"Quicksand",sans-serif;font-weight:600;font-size:42px}
.services-rule{position:absolute;top:132px;left:420px;width:360px;height:2px;background:rgba(255,255,255,.7)}
.service{position:absolute;top:160px;width:300px;text-align:center;color:var(--white)}
.service svg{display:block;margin:0 auto}
.service h3{font-family:"Quicksand",sans-serif;font-weight:600;font-size:30px;margin-top:14px}
.service p{font-size:12px;line-height:1.6;margin:10px auto 0;width:230px;color:#fbe7d6}
.service .btn{margin-top:22px;width:150px;height:46px;line-height:42px;border:2px solid var(--white);color:var(--white);font-size:14px}

/* feature book */
.feature{top:1880px;height:620px;background:var(--grey-bg)}
.feature-art{position:absolute;left:180px;top:80px;width:300px;height:460px;border-radius:4px;background:linear-gradient(150deg,#f7d9c7 0%,#f3c4a8 50%,#e69b62 100%)}
.feature h2{position:absolute;left:580px;top:140px;width:520px;font-family:"Quicksand",sans-serif;font-weight:600;font-size:30px;line-height:1.35;color:var(--orange)}
.feature p{position:absolute;left:580px;top:242px;width:480px;font-size:13px}
.countdown{position:absolute;left:580px;top:410px;display:flex;gap:12px}
.count{width:74px;height:86px;background:var(--white);text-align:center;padding-top:10px;border-radius:3px}
.count b{display:block;font-family:"Quicksand",sans-serif;font-size:30px;color:var(--ink);font-weight:600}
.count span{font-size:10px;letter-spacing:1px;text-transform:uppercase}

/* blog */
.blog{top:2500px;height:500px}
.blog-title{position:absolute;top:28px;left:0;width:1200px;text-align:center;font-family:"Quicksand",sans-serif;font-weight:700;font-size:42px;color:var(--ink)}
.blog-rule{position:absolute;top:90px;left:520px;width:160px;height:3px;background:var(--orange)}
.post{position:absolute;top:130px;width:312px;text-align:center}
.post-img{height:240px}
.post-date{font-family:"Quicksand",sans-serif;font-weight:700;font-size:17px;color:var(--ink);margin-top:14px;border-bottom:2px solid var(--orange);display:inline-block;padding-bottom:4px}
.post p{font-size:12px;line-height:1.6;margin-top:8px}

/* newsletter */
.newsletter{top:3000px;height:360px;background:var(--orange);text-align:center;color:var(--white)}
.newsletter h2{margin-top:36px;font-family:"Quicksand",sans-serif;font-weight:600;font-size:38px}
.newsletter .rule{width:360px;height:2px;background:rgba(255,255,255,.7);margin:10px auto 0}
.newsletter p{width:760px;margin:22px auto 0;font-size:14px;line-height:1.6}
.email-field{position:absolute;left:212px;top:192px;width:776px;height:54px;border-radius:30px;background:var(--white);color:#555;text-align:left;padding-left:28px;line-height:54px;font-size:14px}
.newsletter .btn{position:absolute;left:514px;top:268px;width:172px;height:52px;line-height:52px;background:var(--brown);color:var(--white)}

/* footer */
.footer{top:3360px;height:388px;background:var(--brown-deep);color:#f3dfcd}
.footer .brand{left:122px;top:78px}
.footer .brand-dot{width:86px;height:86px;background:#e7c9a8}
.footer .brand-name{color:var(--white);font-size:24px}
.contact{position:absolute;top:78px;display:flex;gap:14px;font-size:13px;line-height:1.6}
.contact b{font-weight:600;color:var(--white);display:block}
.socials{position:absolute;left:514px;top:178px;display:flex;gap:12px}
.socials span{width:36px;height:36px;border-radius:50%;border:2px solid #f3dfcd}
.footer-rule{position:absolute;left:112px;top:252px;width:976px;height:1px;background:rgba(255,255,255,.25)}
.footer-nav{position:absolute;top:282px;left:0;width:1200px;display:flex;justify-content:center;gap:34px;font-family:"Quicksand",sans-serif;font-weight:600;font-size:14px;color:var(--white)}
.copyright{position:absolute;top:330px;left:0;width:1200px;text-align:center;font-size:12px}
</style>
</head>
<body>

<header class="hero">
  <div class="brand"><span class="brand-dot"></span><span class="brand-name">DWB<br>PRODUCTIONS</span></div>
  <nav class="nav"><span class="active">HOME</span><span>ABOUT US</span><span>SERVICES</span><span>NEWS</span><span>AUTHOR</span><span>CONTACT US</span></nav>
  <div class="hero-title"><div class="name">DORA WHITBY</div><div class="co">PRODUCTIONS</div></div>
  <p class="hero-text">We shape your ideas into books readers trust, with ghostwriting, editing and development for wellness authors who want clear, warm voices.</p>
  <span class="btn">Learn More</span>
  <div class="hero-art" role="img" aria-label="Hardcover book mockup standing beside a framed arched room scene with a pink armchair"></div>
</header>

<section class="about">
  <div class="about-photo" role="img" aria-label="Portrait photograph of the founder in front of bookshelves"></div>
  <h2 class="section-title">ABOUT US</h2>
  <div class="rule"></div>
  <p>Based in Austin, Texas, our team partners with self-help, wellness and diet authors from the first outline to the final proof. We listen closely, learn your message and build a manuscript that sounds like you. Every project gets a dedicated writer and editor, a clear schedule and honest feedback at each stage. Whether you have a rough draft, a set of notes or only a big idea, we help you turn it into a finished book you are proud to share with readers everywhere.</p>
  <span class="btn">Read More</span>
</section>

<section class="services">
  <h2 class="services-title">OUR SERVICES</h2>
  <div class="services-rule"></div>

  <div class="service" style="left:118px">
    <svg width="136" height="136" viewBox="0 0 136 136" aria-hidden="true"><circle cx="68" cy="68" r="64" fill="none" stroke="#fff" stroke-width="3"/><rect x="44" y="42" width="40" height="52" rx="3" fill="none" stroke="#fff" stroke-width="3"/><path d="M52 56h24M52 66h24M52 76h14" stroke="#fff" stroke-width="3"/><path d="M78 86l18-30 6 4-18 30-8 3z" fill="none" stroke="#fff" stroke-width="3" stroke-linejoin="round"/></svg>
    <h3>Writing</h3>
    <p>Full ghostwriting built around your voice, research and goals.</p>
    <span class="btn">Read More</span>
  </div>

  <div class="service" style="left:450px">
    <svg width="136" height="136" viewBox="0 0 136 136" aria-hidden="true"><circle cx="68" cy="68" r="64" fill="none" stroke="#fff" stroke-width="3"/><rect x="42" y="44" width="46" height="50" rx="4" fill="none" stroke="#fff" stroke-width="3"/><path d="M62 78l4-12 24-24 8 8-24 24z" fill="none" stroke="#fff" stroke-width="3" stroke-linejoin="round"/></svg>
    <h3>Editing</h3>
    <p>Careful line and structural edits that sharpen every chapter.</p>
    <span class="btn">Read More</span>
  </div>

  <div class="service" style="left:774px">
    <svg width="136" height="136" viewBox="0 0 136 136" aria-hidden="true"><circle cx="68" cy="68" r="64" fill="none" stroke="#fff" stroke-width="3"/><path d="M68 50c-8-6-18-8-28-8v44c10 0 20 2 28 8 8-6 18-8 28-8V42c-10 0-20 2-28 8zM68 50v44" fill="none" stroke="#fff" stroke-width="3" stroke-linejoin="round"/></svg>
    <h3>Publish</h3>
    <p>Guidance through design, launch and getting your book out.</p>
    <span class="btn">Read More</span>
  </div>
</section>

<section class="feature">
  <div class="feature-art" role="img" aria-label="Book cover with pastel circle pattern in peach, grey and gold"></div>
  <h2>Sed ut perspiciatis unde omnis iste natus error sit voluptate</h2>
  <p>Our newest title arrives soon. Join the launch list for early chapters, author notes and a reader guide. The countdown below shows how long until release day, when copies ship to readers across the country.</p>
  <div class="countdown">
    <div class="count"><b>10</b><span>Days</span></div>
    <div class="count"><b>22</b><span>Hours</span></div>
    <div class="count"><b>05</b><span>Mints</span></div>
    <div class="count"><b>25</b><span>Sec</span></div>
  </div>
</section>

<section class="blog">
  <h2 class="blog-title">LATEST BLOG</h2>
  <div class="blog-rule"></div>
  <article class="post" style="left:112px">
    <div class="post-img" role="img" aria-label="Open book lying on a table in warm light" style="background:linear-gradient(135deg,#c9a27a,#5b3a22)"></div>
    <div class="post-date">08 JULY 2021</div>
    <p>Finding your voice before the first draft begins</p>
  </article>
  <article class="post" style="left:444px">
    <div class="post-img" role="img" aria-label="E-reader resting on a stack of open books" style="background:linear-gradient(135deg,#d8d2c8,#4a4540)"></div>
    <div class="post-date">08 JULY 2021</div>
    <p>Print or digital, choosing the right format</p>
  </article>
  <article class="post" style="left:776px">
    <div class="post-img" role="img" aria-label="Open book in front of full library shelves" style="background:linear-gradient(135deg,#b67a4a,#3f2614)"></div>
    <div class="post-date">08 JULY 2021</div>
    <p>How editors build a stronger book structure</p>
  </article>
</section>

<section class="newsletter">
  <h2>OUR NEWSLETTER</h2>
  <div class="rule"></div>
  <p>Get writing tips, publishing news and author stories delivered to your inbox once a month, with no spam ever.</p>
  <div class="email-field">Enter Your Email</div>
  <span class="btn">Subscribe</span>
</section>

<footer class="footer">
  <div class="brand"><span class="brand-dot"></span><span class="brand-name">DWB<br>PRODUCTIONS</span></div>
  <div class="contact" style="left:480px">
    <svg width="26" height="30" viewBox="0 0 26 30" aria-hidden="true"><path d="M13 2a10 10 0 0 0-10 10c0 8 10 16 10 16s10-8 10-16A10 10 0 0 0 13 2z" fill="none" stroke="#f3dfcd" stroke-width="2"/><circle cx="13" cy="12" r="3.5" fill="none" stroke="#f3dfcd" stroke-width="2"/></svg>
    <div><b>Address:</b>PO Box 214, Cedar Lane<br>Austin TX 78701</div>
  </div>
  <div class="contact" style="left:826px">
    <svg width="26" height="26" viewBox="0 0 26 26" aria-hidden="true"><path d="M6 3l4 0 2 6-3 2a14 14 0 0 0 6 6l2-3 6 2v4a2 2 0 0 1-2 2C11 22 4 15 4 5a2 2 0 0 1 2-2z" fill="none" stroke="#f3dfcd" stroke-width="2" stroke-linejoin="round"/></svg>
    <div><b>Phone:</b>512 555 0148</div>
  </div>
  <div class="contact" style="left:826px;top:150px">
    <svg width="26" height="22" viewBox="0 0 26 22" aria-hidden="true"><rect x="2" y="3" width="22" height="16" rx="2" fill="none" stroke="#f3dfcd" stroke-width="2"/><path d="M2 5l11 8 11-8" fill="none" stroke="#f3dfcd" stroke-width="2"/></svg>
    <div><b>Email:</b>hello@dwbpro.com</div>
  </div>
  <div class="socials"><span></span><span></span></div>
  <div class="footer-rule"></div>
  <nav class="footer-nav"><span>HOME</span><span>ABOUT US</span><span>SERVICES</span><span>NEWS</span><span>AUTHOR</span><span>CONTACT US</span></nav>
  <div class="copyright">DWB Productions © 2021 All Rights Reserved</div>
</footer>

</body>
</html>
```